Chai Tea Company needs a Tea Packaging Box Design

Tea Packaging
Dimensions of the Tea Packaging Box: Height 13 cm; Width 8.5 cm; Depth 7 cm
Individual Teabag Packet/ Sachet: Width 6.5 cm; Length 8.25 cm
We are looking for a new tea packaging design, for our tea business. The material of the box is cardboard. We are also looking for a design that will be on each individual tea bag sachet/packet that goes into the box. This design will be very similar to what you design for the tea packaging box.
Product Info:
Our tea company is called “Velmora Brew”. We sell two types of Chai Tea, once called “Velmora Gold” and one called “Velmora Meadow”. The Velmora Gold has caffeine, while the Velmora Meadow is Naturally Caffeine Free. The Velmora Gold has a black tea base, while the Velmora Meadow has a Rooibos tea base. We will need two tea packaging designs, one for each Chai Tea flavour. The designs for both the teas can be similar, but make sure that you can easily distinguish one from the other (example: make them have different colours or pictures). Both the chai teas, come from the same product line.
Tea Packaging Design:
We are looking for high end tea packaging. We produce high quality teas, and we would like to portray this in our tea packaging. Our teas are made with no artificial flavourings, natural flavourings, or preservatives, so we would also like a natural, organic, high quality look to our tea packaging. Our current logo is a llama. It would be great if you could make the current logo more polished and well made. If you feel that the llama is not well suited or you would like to design the llama differently, we are open to your creative ideas.
General Basic Info:
Keep in mind, we will have both English and French writing on the tea packaging. You do not need to worry about the French writing (we will do the translation), just make sure there is room for it. However, if you feel that you are capable and knowledgeable of incorporating both French and English language into the tea packaging that would be of great help and value.
Back of the Box:
- Will have ingredients and brewing instructions. Basic brewing instructions are: “Add hot water to teabag. Steep for 5-7 minutes, depending on strength preferred. Add milk and your choice of sweetener. Enjoy! See inside panel of box for more detailed instructions”. (The basic brewing instructions, can further be polished or written in a more creative or professional manner).
Front of the Box:
- Will have company name, type of tea, little description of the tea
- 18 teabags
- 54 g (1.9 OZ)
- Should state that this is a product of Alberta, Canada.
Side of the Box:
Any creative wording, slogan, or description about the tea, or whatever you feel would be good on the side of the box.
On the inside flap of the side of the box, there will be detailed instructions on how to brew the tea. These will be different from the simplified brewing instructions on the back of the box. I have attached the advanced brewing instructions as a file. These instructions can further be simplified or reduced to make it easier and cleaner for the consumers to read.
Individual Tea Sachets/ Packets
- These will have a matching look and design of the tea box packaging, except on a smaller scale. Each individual sachet will have the company name, type of tea, little description of the tea in the front of the sachet, while the back will contain the ingredients, and basic brewing instructions.
I have attached a few files, with the dimensions, ingredients, detailed brewing directions, and current logo of the business.
If you have any questions, about the design or packaging please let me know. The winning designer will be required to do a few additional tweaks to finalize the product. Thank you for your time and happy designing!

```html
<!DOCTYPE html>
<html lang="en">
<head>
<meta charset="utf-8">
<title>Velmora Meadow – Tea Box Panels</title>
<link rel="stylesheet" href="https://fonts.googleapis.com/css2?family=Cinzel:wght@600&family=Montserrat:wght@400;600&family=Pinyon+Script&display=swap">
<style>
  :root {
    --stage: #e6e6e6;
    --paper: #f7f6f3;
    --wine: #6e1016;
    --wine-deep: #4e0a0f;
    --llama-red: #b5141c;
    --llama-dark: #8e0c12;
    --gold: #c9ab78;
    --gold-deep: #a8875a;
    --ink: #2a2a2a;
    --ink-soft: #555;
  }
  * { box-sizing: border-box; margin: 0; padding: 0; }
  html, body {
    width: 1200px; height: 1000px; overflow: hidden;
    background: var(--stage);
    font-family: "Montserrat", sans-serif;
  }
  .panel {
    position: absolute; top: 179px;
    width: 420px; height: 642px;
    display: flex;
    box-shadow: 0 6px 24px rgba(0,0,0,.18);
  }
  .panel--front { left: 150px; }
  .panel--back  { left: 630px; }

  .side-band { width: 52px; height: 100%; }
  .side-band--wine { background: linear-gradient(180deg, var(--wine), var(--wine-deep)); }
  .side-band--gold { background: linear-gradient(180deg, var(--gold), var(--gold-deep)); }

  .face {
    flex: 1; height: 100%;
    background: var(--paper);
    display: flex; flex-direction: column; align-items: center;
  }

  /* front */
  .product-title {
    margin-top: 42px;
    font-family: "Pinyon Script", cursive;
    color: var(--wine);
    font-size: 62px; line-height: .95;
    text-align: center;
  }
  .llama-art { margin-top: 16px; }
  .brand-name {
    font-family: "Cinzel", serif; font-weight: 600;
    color: var(--ink);
    letter-spacing: 1px;
    display: flex; align-items: center; gap: 8px;
  }
  .brand-name .mark-dot {
    width: 10px; height: 10px; border-radius: 50%;
    background: var(--llama-red);
  }
  .brand-name--front { font-size: 34px; margin-top: 14px; }
  .count {
    margin-top: 20px;
    font-family: "Cinzel", serif; font-size: 34px; color: var(--ink); line-height: 1;
  }
  .count-label { font-size: 13px; letter-spacing: 3px; color: var(--ink-soft); margin-top: 4px; }
  .net-weight { font-size: 11px; color: var(--ink-soft); margin-top: 10px; letter-spacing: 1px; }

  /* back */
  .llama-art--small { margin-top: 40px; }
  .brand-name--back { font-size: 26px; margin-top: 10px; }
  .variety-label {
    margin-top: 14px;
    font-family: "Cinzel", serif; font-weight: 600; font-size: 15px;
    letter-spacing: 1px; color: var(--ink);
  }
  .copy { width: 250px; margin-top: 14px; color: var(--ink); }
  .copy p, .copy li { font-size: 10px; line-height: 1.45; text-transform: uppercase; letter-spacing: .3px; }
  .copy .intro { font-size: 11.5px; line-height: 1.4; }
  .copy h3 { font-size: 11px; font-weight: 600; margin: 12px 0 4px; letter-spacing: .5px; }
  .copy ul { list-style: none; }
  .copy ol { list-style: none; }
  .copy .small li { font-size: 8.5px; line-height: 1.5; }
</style>
</head>
<body>

<section class="panel panel--front" aria-label="Front panel">
  <div class="side-band side-band--wine" role="img" aria-label="Deep red patterned side band"></div>
  <div class="face">
    <h1 class="product-title">Velmora<br>Meadow</h1>
    <svg class="llama-art" width="200" height="230" viewBox="0 0 200 230" role="img" aria-label="Illustration of a standing red llama">
      <defs>
        <linearGradient id="llamaFront" x1="0" y1="0" x2="0" y2="1">
          <stop offset="0" stop-color="#c41a22"/>
          <stop offset="1" stop-color="#8e0c12"/>
        </linearGradient>
      </defs>
      <rect x="20" y="0" width="160" height="230" rx="30" fill="url(#llamaFront)"/>
    </svg>
    <div class="brand-name brand-name--front"><span class="mark-dot"></span>VELMORA BREW</div>
    <div class="count">18</div>
    <div class="count-label">TEABAGS</div>
    <div class="net-weight">54 G (1.9 OZ)</div>
  </div>
  <div class="side-band side-band--wine" role="img" aria-label="Deep red patterned side band"></div>
</section>

<section class="panel panel--back" aria-label="Back panel">
  <div class="side-band side-band--gold" role="img" aria-label="Gold patterned side band"></div>
  <div class="face">
    <svg class="llama-art llama-art--small" width="100" height="100" viewBox="0 0 100 100" role="img" aria-label="Small illustration of a red llama">
      <defs>
        <linearGradient id="llamaBack" x1="0" y1="0" x2="0" y2="1">
          <stop offset="0" stop-color="#c41a22"/>
          <stop offset="1" stop-color="#8e0c12"/>
        </linearGradient>
      </defs>
      <rect x="10" y="0" width="80" height="100" rx="16" fill="url(#llamaBack)"/>
    </svg>
    <div class="brand-name brand-name--back"><span class="mark-dot"></span>VELMORA BREW</div>
    <h2 class="variety-label">VELMORA MEADOW</h2>
    <div class="copy">
      <p class="intro">Chai is a rich blend of strong and flavourful tea, aromatic spices, milk and sugar. Authentic chai is an art that requires all natural ingredients, care and time to prepare.</p>
      <h3>FOR 2 CUPS:</h3>
      <h3>INGREDIENTS:</h3>
      <ul class="small">
        <li>3 cups (12 oz) water</li>
        <li>2 chai tea bags</li>
        <li>1 cup (8 oz) whole milk</li>
        <li>2-4 teaspoons sugar or honey to taste</li>
        <li>1-2 teaspoons sliced or grated fresh ginger (optional)</li>
      </ul>
      <h3>DIRECTIONS:</h3>
      <ol class="small">
        <li>1. Bring water and tea bags to a low boil in a covered pot.</li>
        <li>2. Turn down heat, keep covered and simmer for 5 minutes. Stir and gently press bags to release flavour.</li>
        <li>3. Add ginger and milk, stir and heat until chai starts to steam.</li>
        <li>4. Add sugar or honey, stir and let sit covered for 3 to 5 minutes.</li>
        <li>5. Remove bags and pour into cups. Enjoy while warm.</li>
      </ol>
    </div>
  </div>
  <div class="side-band side-band--gold" role="img" aria-label="Gold patterned side band"></div>
</section>

</body>
</html>
```